Business card for Eyelash extension salon in Beverly Hills,California USA

We need new business card for our salon in Beverly Hills. The salon name is 'Lashvera' . We would like to have...Business name: Lashvera Name of person: will provide later Address 4720 N.Alder Crest Ave Beverly Hills , CA 90210 Phone: will provide later (Text only) Web: www.lashverastudio.example Snapgrid icon, Circlebook icon follow us for seasonal campaign and news @lashverastudiolounge Design should look elegant, high-end, clean, simple, cohesive with my brand. Please refer my brand board. Business name color will be metallic bronzy color. Im thinking grey background or white background. Thanks

Target Market(s)

25-35. Gender neutral. People who are in Entertainment business industry.
This is High-end Eyelash extension salon in Beverly Hills

Industry/Entity Type

Beauty Salon

Contact Information for Business Card

Business name: Lashvera
Name of person: will provide later
Address 4720 N.Alder Crest Ave Beverly Hills , CA 90210
Phone: will provide later (Text only)
Web: www.lashverastudio.example
Snapgrid icon, Circlebook icon
follow us for seasonal campaign and news @lashverastudiolounge

Requirements
Must have
• Beautiful, elegant, clean and simple look but very attractive and modern
Should not have
• We don't like too clutter, too busy designs.

```html
<!DOCTYPE html>
<html lang="en">
<head>
<meta charset="utf-8">
<title>Lashvera Business Card</title>
<link rel="stylesheet" href="https://fonts.googleapis.com/css2?family=Montserrat:wght@300;400;600&display=swap">
<style>
  :root {
    --page: #ece8e3;
    --card-dark: #1f1f1f;
    --card-grey: #a4a4a4;
    --bronze: #a57e62;
    --bronze-light: #c29a7c;
    --text-light: #d6d6d6;
    --white: #ffffff;
  }
  * { margin: 0; padding: 0; box-sizing: border-box; }
  html, body { width: 1200px; height: 960px; overflow: hidden; }
  body {
    background: var(--page);
    font-family: "Montserrat", Arial, sans-serif;
    position: relative;
  }
  .card {
    position: absolute;
    left: 220px;
    width: 760px;
    height: 434px;
    border-radius: 4px;
    box-shadow: 0 8px 24px rgba(0,0,0,0.18);
    overflow: hidden;
  }
  /* back side */
  .card-back { top: 36px; background: var(--card-grey); color: var(--white); text-align: center; }
  .back-logo {
    position: absolute; top: 92px; left: 0; right: 0;
    font-size: 88px; font-weight: 300; letter-spacing: 2px; line-height: 1;
  }
  .back-place {
    position: absolute; top: 196px; left: 0; right: 0;
    font-size: 13px; letter-spacing: 4px;
  }
  .social-row {
    position: absolute; top: 258px; left: 0; right: 0;
    display: flex; justify-content: center; gap: 28px;
    font-size: 14px;
  }
  .social { display: flex; align-items: center; gap: 8px; }
  .social-dot { width: 22px; height: 22px; border: 1.5px solid var(--white); border-radius: 50%; }
  .follow-line { position: absolute; top: 306px; left: 0; right: 0; font-size: 17px; }
  .handle { position: absolute; top: 334px; left: 0; right: 0; font-size: 17px; }

  /* front side */
  .card-front { top: 490px; background: var(--card-dark); }
  .person-name {
    position: absolute; top: 62px; left: 58px;
    color: var(--bronze); font-size: 30px; font-weight: 600; letter-spacing: 2.5px;
  }
  .person-role {
    position: absolute; top: 104px; left: 58px;
    color: var(--text-light); font-size: 16px; letter-spacing: 0.5px;
  }
  .divider { position: absolute; top: 170px; left: 58px; width: 62px; height: 1px; background: var(--bronze); }
  .address {
    position: absolute; top: 238px; left: 58px;
    color: var(--text-light); font-size: 19px; line-height: 30px; font-weight: 400;
  }
  .contact {
    position: absolute; left: 58px; display: flex; align-items: center; gap: 16px;
    color: var(--text-light); font-size: 19px;
  }
  .contact-phone { top: 318px; }
  .contact-web { top: 352px; }
  .contact svg { width: 16px; height: 16px; }
  .front-logo {
    position: absolute; top: 108px; left: 440px; width: 300px; text-align: center;
    color: var(--bronze); font-size: 64px; font-weight: 300; letter-spacing: 1px; line-height: 1;
  }
  .front-place {
    position: absolute; top: 186px; left: 440px; width: 300px; text-align: center;
    color: var(--bronze); font-size: 12px; letter-spacing: 3px;
  }
  .figures {
    position: absolute; left: 462px; bottom: 0; width: 270px; height: 188px;
    background: linear-gradient(180deg, rgba(165,126,98,0.55), var(--bronze) 70%, rgba(165,126,98,0.85));
    border-radius: 40px 40px 0 0;
    opacity: 0.9;
  }
</style>
</head>
<body>

<section class="card card-back">
  <div class="back-logo">Lashvera</div>
  <div class="back-place">BEVERLY HILLS</div>
  <div class="social-row">
    <span class="social"><span class="social-dot"></span>Circlebook</span>
    <span class="social"><span class="social-dot"></span>Snapgrid</span>
  </div>
  <p class="follow-line">Follow Us For Seasonal Campaign News</p>
  <p class="handle">@lashverastudiolounge</p>
</section>

<section class="card card-front">
  <h1 class="person-name">Corinne Maddox</h1>
  <p class="person-role">Fashion Marketing</p>
  <div class="divider"></div>
  <p class="address">4720 N.Alder Crest Ave<br>Beverly Hills , CA 90210</p>
  <p class="contact contact-phone">
    <svg viewBox="0 0 16 16" aria-hidden="true"><path d="M3.5 1.5l2.5 3-1.6 1.6c.8 1.8 2.2 3.2 4 4l1.6-1.6 3 2.5-1.5 2.5C6.8 13.2 2.8 9.2 1 4.5z" fill="#a57e62"/></svg>
    1 555 014 2290
  </p>
  <p class="contact contact-web">
    <svg viewBox="0 0 16 16" aria-hidden="true" fill="none" stroke="#a57e62" stroke-width="1.2"><circle cx="8" cy="8" r="6.5"/><ellipse cx="8" cy="8" rx="3" ry="6.5"/><path d="M1.5 8h13M2.5 4.8h11M2.5 11.2h11"/></svg>
    www.lashverastudio.example
  </p>
  <div class="front-logo">Lashvera</div>
  <div class="front-place">BEVERLY HILLS</div>
  <div class="figures" role="img" aria-label="Bronze silhouettes of two fashion models posing"></div>
</section>

</body>
</html>
```